The Linen Loft Co

We need a business card design for our wardrobe company.
Please visit our website www.gentlelinenlofts.com to get an idea of who we are.

```html
<!DOCTYPE html>
<html lang="en">
<head>
<meta charset="utf-8">
<title>The Linen Loft Co — Business Card</title>
<link rel="stylesheet" href="https://fonts.googleapis.com/css2?family=Lato:wght@400;700&display=swap">
<style>
  :root {
    --page-bg: #2b2624;
    --card-bg: #0e0e0e;
    --card-edge: #1c1c1c;
    --ink-bright: #f2f2f2;
    --ink-soft: #a9a9a9;
    --ink-muted: #8a8a8a;
    --rule: #555555;
  }
  * { box-sizing: border-box; margin: 0; padding: 0; }
  html, body { width: 1200px; height: 844px; overflow: hidden; }
  body {
    background: var(--page-bg);
    font-family: "Lato", Arial, sans-serif;
    position: relative;
  }
  .card {
    position: absolute;
    top: 273px;
    width: 520px;
    height: 298px;
    background: var(--card-bg);
    border: 1px solid var(--card-edge);
    box-shadow: 0 14px 30px rgba(0,0,0,0.45);
  }
  .card--front { left: 60px; }
  .card--back { left: 620px; }

  .brand {
    position: absolute;
    left: 150px;
    top: 62px;
    display: flex;
    align-items: center;
    gap: 14px;
  }
  .brand__square {
    width: 46px;
    height: 46px;
    border: 2px solid var(--ink-bright);
    flex: none;
  }
  .brand__name {
    color: var(--ink-bright);
    font-weight: 700;
    font-size: 15px;
    letter-spacing: 0.3px;
    text-transform: uppercase;
  }
  .brand__tagline {
    color: var(--ink-bright);
    font-size: 12px;
    margin-top: 3px;
  }
  .brand-rule {
    position: absolute;
    left: 160px;
    top: 128px;
    width: 200px;
    height: 1px;
    background: var(--rule);
  }

  .person {
    position: absolute;
    left: 28px;
    top: 178px;
  }
  .person__name {
    color: var(--ink-bright);
    font-weight: 700;
    font-size: 16px;
    text-transform: uppercase;
  }
  .person__role {
    color: var(--ink-muted);
    font-size: 13px;
    margin-top: 1px;
  }
  .person-rule {
    position: absolute;
    left: 175px;
    top: 190px;
    width: 170px;
    height: 1px;
    background: var(--rule);
  }

  .contacts {
    position: absolute;
    left: 28px;
    top: 228px;
    list-style: none;
  }
  .contacts li {
    display: flex;
    align-items: center;
    gap: 9px;
    color: var(--ink-soft);
    font-size: 13px;
    line-height: 19px;
  }
  .contacts svg { width: 10px; height: 10px; fill: var(--ink-soft); flex: none; }

  .address {
    position: absolute;
    right: 26px;
    top: 168px;
    text-align: right;
    color: var(--ink-soft);
    font-size: 13px;
    line-height: 18px;
    font-style: normal;
  }

  .back-brand {
    position: absolute;
    inset: 0;
    display: flex;
    align-items: center;
    justify-content: center;
    gap: 16px;
  }
  .back-brand__square {
    width: 54px;
    height: 54px;
    border: 2px solid var(--ink-bright);
  }
  .back-brand__name {
    color: var(--ink-bright);
    font-weight: 700;
    font-size: 22px;
    letter-spacing: 0.5px;
    text-transform: uppercase;
  }
</style>
</head>
<body>
  <section class="card card--front" aria-label="Card front">
    <div class="brand">
      <span class="brand__square"></span>
      <div>
        <div class="brand__name">The Linen Loft Co</div>
        <div class="brand__tagline">Calm order in every room</div>
      </div>
    </div>
    <div class="brand-rule"></div>

    <div class="person">
      <div class="person__name">Edward Hale</div>
      <div class="person__role">Managing Director</div>
    </div>
    <div class="person-rule"></div>

    <ul class="contacts">
      <li>
        <svg viewBox="0 0 10 10" aria-hidden="true"><path d="M1 3 Q5 0 9 3 L8 4.5 L6.5 3.8 L6.5 3 Q5 2.5 3.5 3 L3.5 3.8 L2 4.5 Z M2.5 5 H7.5 L8.5 9 H1.5 Z"/></svg>
        0207 555 0148
      </li>
      <li>
        <svg viewBox="0 0 10 10" aria-hidden="true"><path d="M0.5 2 H9.5 V8.5 H0.5 Z M1 2.5 L5 5.5 L9 2.5" stroke="#0e0e0e" stroke-width="0.8"/></svg>
        info@gentlelinenlofts.com
      </li>
      <li>
        <svg viewBox="0 0 10 10" aria-hidden="true"><circle cx="5" cy="5" r="4.5"/></svg>
        www.gentlelinenlofts.com
      </li>
    </ul>

    <address class="address">
      Marlow Court, 42 Ferris Lane<br>
      London N4 7QT
    </address>
  </section>

  <section class="card card--back" aria-label="Card back">
    <div class="back-brand">
      <span class="back-brand__square"></span>
      <span class="back-brand__name">The Linen Loft Co</span>
    </div>
  </section>
</body>
</html>
```